New Website Design for PHOVAN.org

We are looking for a new website design for PHOVAN.org. PHOVAN is a non profit home inspector association based in California. Home Inspectors are people that come out and look at a house before it's purchased to let the buyer know of any defects that may exist.
Our site is based on Joomla so if you'll be able to make a Joomla 3 template as well, please let us know (not required, but a bonus).
We would like to see designs that incorporate royal blue, white and chrome into the site as that's our main business colors.
We would like a place for rotating banners though they don't need to be the same size as the current site.
We would like navigation to be easier to manage with menus only across the top (via drop down menus) where we are going to sort out the items currently on the side. Possibly the front page could have a graphic link to separate portals for Realtors, Home Buyers and Inspectors, but that's just one option.
We would like a good mobile design or something that will scale easily to mobile.
The Find an Inspector feature is important and should stand out. The ASK PHOVANr site
Current home page feels a bit busy. Would like to simplify a bit.

```html
<!DOCTYPE html>
<html lang="en">
<head>
<meta charset="utf-8">
<title>PHOVAN – Home Inspector Association</title>
<link href="https://fonts.googleapis.com/css2?family=Open+Sans:wght@400;600;700&display=swap" rel="stylesheet">
<style>
:root{
  --royal:#3b2d7c;
  --royal-dark:#2c2160;
  --accent:#c8282d;
  --ink:#333;
  --muted:#8a8a8a;
  --line:#e2e2e2;
  --panel:#f3f3f3;
  --footer:#262626;
  --footer-base:#1b1b1b;
  --footer-text:#a9a9a9;
}
*{box-sizing:border-box;margin:0;padding:0}
html,body{width:845px;height:1200px;overflow:hidden}
body{font-family:"Open Sans",Arial,sans-serif;color:var(--ink);background:#fff;position:relative}
a{color:inherit;text-decoration:none}

/* header */
.site-header{height:84px;display:flex;align-items:center;justify-content:space-between;padding:0 28px}
.brand{display:flex;align-items:center;gap:10px}
.brand-mark{width:50px;height:50px;border-radius:50%;background:var(--royal)}
.brand-name{font-size:18px;font-weight:700;color:var(--royal)}
.main-nav{display:flex;gap:22px;font-size:8.5px;font-weight:600;text-transform:uppercase;letter-spacing:.3px}
.main-nav a{padding:6px 0;color:#555}
.main-nav a.is-active{color:var(--royal);border-bottom:2px solid var(--royal)}

/* hero */
.hero{position:relative;height:230px}
.hero-photo{position:absolute;inset:0;background:linear-gradient(90deg,#c4c6c8 0%,#d9dadb 25%,#ececec 50%,#f3f3f3 100%)}
.hero-title{position:absolute;left:455px;top:150px;font-size:12px;font-weight:600;text-transform:uppercase;color:#3a3a3a;line-height:1.45;letter-spacing:.3px}
.hero-title strong{display:block;font-size:17px;font-weight:600;color:#2f2f2f}
.hero-dots{position:absolute;bottom:12px;left:50%;transform:translateX(-50%);display:flex;gap:6px}
.hero-dots span{width:7px;height:7px;border-radius:50%;background:#fff;border:1px solid #999}
.hero-dots span.on{background:var(--royal);border-color:var(--royal)}

/* portals */
.portals{display:flex;padding:16px 28px 14px;border-bottom:1px solid var(--line)}
.portal{flex:1;display:flex;gap:8px;align-items:flex-start}
.portal-photo{width:32px;height:32px;border-radius:50%;flex:none;background:linear-gradient(135deg,#c9c9c9,#8f8f8f)}
.portal h3{font-size:10px;font-weight:600;color:#444;margin-top:2px}
.portal p{font-size:7.5px;color:var(--muted);line-height:1.4;margin-top:2px}

/* main */
.content{display:flex;gap:28px;padding:18px 28px 0}
.primary{width:522px}
.section-title{font-size:17px;font-weight:400;color:var(--royal);padding-bottom:6px;border-bottom:1px solid var(--line);margin-bottom:10px}
.intro{font-size:8.5px;line-height:1.6;color:var(--muted)}
.feature-grid{display:grid;grid-template-columns:1fr 1fr;gap:26px 22px;margin-top:26px}
.feature h3{font-size:11px;font-weight:600;color:#444;margin-bottom:8px}
.feature-image{width:200px;height:112px}
.img-study{background:linear-gradient(135deg,#d7c7ad,#7d6a55)}
.img-books{background:linear-gradient(135deg,#b89a6b,#6b4f33)}
.img-store{background:linear-gradient(135deg,#f4f4f4,#cfe3c8)}
.img-ask{background:linear-gradient(135deg,#f7f7f7,#e0b6b6)}
.feature p{font-size:7.5px;line-height:1.55;color:var(--muted);margin-top:8px;width:230px}
.feature .more{font-size:7.5px;color:var(--accent);font-weight:600;margin-top:3px;display:block}

.sidebar{width:240px}
.widget{margin-bottom:16px}
.widget-title{background:var(--royal);color:#fff;font-size:10px;font-weight:600;padding:7px 10px}
.widget-body{background:var(--panel);padding:8px 10px}
.resource-list{list-style:none}
.resource-list li{font-size:8px;color:#555;padding:5px 0 5px 12px;border-bottom:1px solid #e4e4e4;position:relative}
.resource-list li:last-child{border-bottom:0}
.resource-list li::before{content:"";position:absolute;left:0;top:9px;width:5px;height:5px;background:var(--royal);border-radius:50%}
.event-list{list-style:none}
.event-list li{padding:6px 0;border-bottom:1px solid #e4e4e4}
.event-list li:last-child{border-bottom:0}
.event-list .event-name{font-size:7.5px;color:#666}
.event-list .event-date{font-size:7.5px;color:var(--accent);font-weight:600;margin-top:2px;display:block}
.search-form label{display:block;font-size:7.5px;color:#666;margin:4px 0 3px}
.search-form .field{height:20px;background:#fff;border:1px solid #d4d4d4;font-size:7.5px;color:#999;padding:4px 6px;margin-bottom:4px}
.search-form .button{display:inline-block;margin-top:6px;background:var(--accent);color:#fff;font-size:8px;font-weight:600;padding:5px 14px}

/* footer */
.site-footer{position:absolute;left:0;right:0;top:1052px;height:128px;background:var(--footer);display:flex;gap:24px;padding:16px 28px 0}
.footer-col{flex:1}
.footer-col h4{color:#fff;font-size:10px;font-weight:600;margin-bottom:8px}
.footer-col p,.footer-col li{font-size:7.5px;line-height:1.6;color:var(--footer-text);list-style:none}
.footer-base{position:absolute;left:0;right:0;top:1180px;height:20px;background:var(--footer-base);color:#777;font-size:7px;text-align:center;line-height:20px}
</style>
</head>
<body>

<header class="site-header">
  <a class="brand" href="#"><span class="brand-mark"></span><span class="brand-name">PHOVAN</span></a>
  <nav class="main-nav">
    <a class="is-active" href="#">Home</a>
    <a href="#">Find an Inspector</a>
    <a href="#">Home Buyers &amp; Seller</a>
    <a href="#">Real Estate Agents</a>
    <a href="#">Ask PHOVAN</a>
    <a href="#">Conferences</a>
  </nav>
</header>

<section class="hero">
  <div class="hero-photo" role="img" aria-label="Banner photo of a home inspector measuring a wall"></div>
  <h1 class="hero-title"><strong>The symbol of real estate</strong>inspection professionalism<br>in state of California</h1>
  <div class="hero-dots"><span class="on"></span><span></span><span></span></div>
</section>

<section class="portals">
  <div class="portal"><span class="portal-photo" role="img" aria-label="Inspector portrait"></span><div><h3>Find An Inspector</h3><p>Search certified members near your property today.</p></div></div>
  <div class="portal"><span class="portal-photo" role="img" aria-label="Home buyers portrait"></span><div><h3>Home Buyers and Sellers</h3><p>Know what to expect before you close.</p></div></div>
  <div class="portal"><span class="portal-photo" role="img" aria-label="Real estate agent portrait"></span><div><h3>Real Estate Agents</h3><p>Share trusted reports with your clients.</p></div></div>
  <div class="portal"><span class="portal-photo" role="img" aria-label="New member portrait"></span><div><h3>Become A Member</h3><p>Join the state's leading inspector group.</p></div></div>
</section>

<main class="content">
  <div class="primary">
    <h2 class="section-title">About PHOVAN</h2>
    <p class="intro">Our association brings together home inspectors across the state who share one standard of care. Members follow a clear code of ethics, complete yearly education and help buyers understand the real condition of a home before they sign. Learn how membership supports your work and your clients every day.</p>

    <div class="feature-grid">
      <article class="feature">
        <h3>Path To Success</h3>
        <div class="feature-image img-study" role="img" aria-label="Student studying with laptop and books"></div>
        <p>Practical steps, mentoring and tools that help new inspectors build a steady, trusted business from the first report.</p>
        <a class="more" href="#">Read more</a>
      </article>
      <article class="feature">
        <h3>Educational Publications</h3>
        <div class="feature-image img-books" role="img" aria-label="Stack of open books"></div>
        <p>Guides, manuals and standards written by members to keep every inspection clear, current and consistent.</p>
        <a class="more" href="#">Read more</a>
      </article>
      <article class="feature">
        <h3>PHOVAN Online Store</h3>
        <div class="feature-image img-store" role="img" aria-label="Online store graphic with shopping bag"></div>
        <p>Order forms, report books, tools and branded items for your daily inspection work in the field.</p>
        <a class="more" href="#">Read more</a>
      </article>
      <article class="feature">
        <h3>Ask PHOVAN</h3>
        <div class="feature-image img-ask" role="img" aria-label="Figure beside a large question mark"></div>
        <p>Send your questions to experienced inspectors and get plain answers about homes, systems and repairs.</p>
        <a class="more" href="#">Read more</a>
      </article>
    </div>
  </div>

  <aside class="sidebar">
    <div class="widget">
      <h3 class="widget-title">Other Inspection Resources</h3>
      <div class="widget-body">
        <ul class="resource-list">
          <li>California Real Estate Inspection Law</li>
          <li>Chapter Meeting Locations</li>
          <li>Standards of Practice</li>
          <li>Code of Ethics</li>
          <li>Education / CEU's</li>
        </ul>
      </div>
    </div>

    <div class="widget">
      <h3 class="widget-title">Upcoming Events</h3>
      <div class="widget-body">
        <ul class="event-list">
          <li><span class="event-name">Regional chapter meeting and member dinner</span><span class="event-date">09-08-2013</span></li>
          <li><span class="event-name">Roofing systems workshop for new members</span><span class="event-date">09-08-2013</span></li>
          <li><span class="event-name">Electrical safety seminar with field demos</span><span class="event-date">09-08-2013</span></li>
          <li><span class="event-name">Annual board election and open forum</span><span class="event-date">09-08-2013</span></li>
        </ul>
      </div>
    </div>

    <div class="widget">
      <h3 class="widget-title">Find an Inspector</h3>
      <div class="widget-body search-form">
        <label>Inspector Name</label>
        <div class="field">Inspector Name</div>
        <label>Inspector City</label>
        <div class="field">City or Zip Code</div>
        <span class="button">Search</span>
      </div>
    </div>
  </aside>
</main>

<footer class="site-footer">
  <div class="footer-col">
    <h4>Popular</h4>
    <ul>
      <li>Inspector FAQs</li>
      <li>Common Home Defects</li>
      <li>Becoming a Member</li>
      <li>Education / CEUs</li>
      <li>Affiliate Directory</li>
    </ul>
  </div>
  <div class="footer-col">
    <h4>Business method</h4>
    <p>We inspect with care, report in plain words and stand behind every finding we share with buyers and agents.</p>
  </div>
  <div class="footer-col">
    <h4>Get in touch</h4>
    <p>4100 Oak Street, Suite 210<br>Sacramento CA 95800<br>Phone: (555) 014-2270<br>Fax: (555) 014-2271<br>info@phovan.org</p>
  </div>
  <div class="footer-col">
    <h4>Who We are</h4>
    <p>Founded as a non profit, PHOVAN is a statewide group of home inspectors working to raise standards and protect home buyers throughout California.</p>
  </div>
</footer>
<div class="footer-base">Copyright © 2014 PHOVAN. All rights reserved.</div>

</body>
</html>
```